"Got Radon?" Banner Ads

I need banner ads made for Brimwell Adspace Circuit campaign. There are 10 sizes of banners, so I need all 10 sizes. All of them can be similar in design and concept, but need to look good and the content must fill the space nicely.

The text on the ad is "Got Radon?" big/bold, and there should be a picture of a house with gas seeping into it from the ground. I have attached an example of an existing ad for reference.

These are the 10 sizes of banners that we need:
970x90
120x600
160x600
200x200
250x250
350x250
300x600
336x280
468x60
728x90

```html
<!DOCTYPE html>
<html lang="en">
<head>
<meta charset="utf-8">
<title>Got Radon? Banner Set</title>
<link href="https://fonts.googleapis.com/css2?family=Righteous&family=Archivo+Black&family=Montserrat:wght@500;800&display=swap" rel="stylesheet">
<style>
  :root {
    --board: #353535;
    --brand-green: #179b17;
    --head-green: #17a017;
    --label: #d4f7a8;
    --ink: #111111;
    --paper: #ffffff;
    --art-sky: #c6d2c2;
    --art-shade: #4d7a52;
    --art-roof: #6d8a70;
    --art-gas: #3fc23a;
    --art-glow: #55d04a;
  }
  * { margin: 0; padding: 0; box-sizing: border-box; }
  html, body { width: 1200px; height: 1200px; overflow: hidden; background: var(--board); }
  .board { position: relative; width: 1200px; height: 1200px; background: var(--board); }

  .banner { position: absolute; background: var(--brand-green); overflow: hidden; }
  .art { position: absolute; left: 0; top: 0; width: 100%; }
  .art--tall {
    background:
      radial-gradient(ellipse 30% 18% at 22% 22%, rgba(60,90,64,.75), transparent 70%),
      radial-gradient(ellipse 28% 20% at 70% 18%, rgba(70,100,74,.7), transparent 70%),
      radial-gradient(ellipse 35% 16% at 45% 48%, rgba(55,95,60,.7), transparent 70%),
      radial-gradient(ellipse 26% 14% at 85% 55%, rgba(60,105,64,.6), transparent 70%),
      radial-gradient(ellipse 40% 22% at 30% 70%, rgba(85,208,74,.8), transparent 70%),
      radial-gradient(ellipse 40% 22% at 78% 75%, rgba(85,208,74,.8), transparent 70%),
      linear-gradient(180deg, var(--art-sky) 0%, var(--art-roof) 20%, var(--art-gas) 45%, var(--art-shade) 62%, var(--art-gas) 82%, var(--brand-green) 100%);
  }
  .art--wide {
    height: 100%;
    background:
      radial-gradient(ellipse 14% 45% at 10% 40%, rgba(60,90,64,.75), transparent 70%),
      radial-gradient(ellipse 14% 45% at 40% 35%, rgba(70,100,74,.7), transparent 70%),
      radial-gradient(ellipse 14% 45% at 72% 40%, rgba(60,90,64,.7), transparent 70%),
      radial-gradient(ellipse 30% 40% at 50% 90%, rgba(85,208,74,.9), transparent 70%),
      linear-gradient(180deg, var(--art-sky) 0%, var(--art-roof) 30%, var(--art-gas) 70%, var(--art-glow) 100%);
  }

  .headline {
    position: absolute; transform: translate(-50%, -50%);
    font-family: "Righteous", sans-serif; white-space: nowrap; line-height: 1;
    color: var(--paper); -webkit-text-stroke: 5px var(--ink); paint-order: stroke fill;
  }
  .tagline {
    position: absolute; transform: translate(-50%, -50%);
    font-family: "Montserrat", sans-serif; font-weight: 500; color: var(--paper);
    letter-spacing: 1px; white-space: nowrap;
  }
  .letter {
    position: absolute; transform: translate(-50%, -50%);
    font-family: "Righteous", sans-serif; font-size: 42px; line-height: 1;
    color: var(--paper); -webkit-text-stroke: 5px var(--ink); paint-order: stroke fill;
  }
  .size-label {
    position: absolute; font-family: "Montserrat", sans-serif; font-weight: 800;
    font-size: 16px; color: var(--label); white-space: nowrap;
  }
  .campaign-title {
    position: absolute; left: 60px; top: 604px;
    font-family: "Archivo Black", sans-serif; color: var(--head-green);
    font-size: 77px; line-height: 82px;
  }
  .campaign-sub {
    position: absolute; left: 61px; top: 772px;
    font-family: "Archivo Black", sans-serif; color: var(--head-green);
    font-size: 29px; line-height: 36px;
  }
</style>
</head>
<body>
<main class="board">

  <!-- 350 x 250 -->
  <section class="banner" style="left:60px;top:38px;width:280px;height:200px">
    <div class="art art--tall" style="height:170px" role="img" aria-label="Sketched neighbourhood of houses with green radon gas rising from the ground"></div>
    <div class="headline" style="left:140px;top:158px;font-size:41px">GOT RADON?</div>
  </section>
  <div class="size-label" style="left:60px;top:247px">350 X 250</div>

  <!-- 336 x 280 -->
  <section class="banner" style="left:422px;top:38px;width:269px;height:224px">
    <div class="art art--tall" style="height:175px" role="img" aria-label="Sketched neighbourhood of houses with green radon gas rising from the ground"></div>
    <div class="headline" style="left:134px;top:166px;font-size:40px">GOT RADON?</div>
    <div class="tagline" style="left:134px;top:203px;font-size:15px">RADON REDUCTION</div>
  </section>
  <div class="size-label" style="left:426px;top:275px">336 X 280</div>

  <!-- 250 x 250 -->
  <section class="banner" style="left:60px;top:337px;width:200px;height:200px">
    <div class="art art--tall" style="height:150px" role="img" aria-label="Sketched houses with green radon gas seeping up"></div>
    <div class="headline" style="left:100px;top:164px;font-size:29px;-webkit-text-stroke-width:4px">GOT RADON?</div>
  </section>
  <div class="size-label" style="left:60px;top:546px">250 X 250</div>

  <!-- 200 x 200 -->
  <section class="banner" style="left:340px;top:337px;width:160px;height:160px">
    <div class="art art--tall" style="height:122px" role="img" aria-label="Sketched houses with green radon gas seeping up"></div>
    <div class="headline" style="left:80px;top:134px;font-size:24px;-webkit-text-stroke-width:4px">GOT RADON?</div>
  </section>
  <div class="size-label" style="left:343px;top:509px">200 X 200</div>

  <!-- 300 x 600 -->
  <section class="banner" style="left:910px;top:38px;width:240px;height:480px">
    <div class="art art--tall" style="height:340px" role="img" aria-label="Tall sketched neighbourhood of houses with green radon gas rising from the ground"></div>
    <div class="headline" style="left:122px;top:304px;font-size:79px;-webkit-text-stroke-width:7px">GOT</div>
    <div class="headline" style="left:122px;top:372px;font-size:54px;-webkit-text-stroke-width:6px">RADON?</div>
    <div class="tagline" style="left:122px;top:427px;font-size:15px;letter-spacing:0">RADON REDUCTION</div>
  </section>
  <div class="size-label" style="left:910px;top:534px">300 X 600</div>

  <!-- Campaign title -->
  <h1 class="campaign-title">GOT<br>RADON?</h1>
  <p class="campaign-sub">Brimwell Adspace<br>Circuit campaign</p>

  <!-- 468 x 60 -->
  <div class="size-label" style="left:462px;top:800px">468 X 60</div>
  <section class="banner" style="left:462px;top:831px;width:374px;height:48px">
    <div class="art art--wide" style="width:170px" role="img" aria-label="Row of sketched houses with green gas"></div>
    <div class="headline" style="left:260px;top:24px;font-size:32px;-webkit-text-stroke-width:4px">GOT RADON?</div>
  </section>

  <!-- 728 x 90 -->
  <div class="size-label" style="left:270px;top:916px">728 X 90</div>
  <section class="banner" style="left:266px;top:943px;width:582px;height:72px">
    <div class="art art--wide" style="width:234px" role="img" aria-label="Row of sketched houses with green gas"></div>
    <div class="headline" style="left:406px;top:37px;font-size:50px;-webkit-text-stroke-width:6px">GOT RADON?</div>
  </section>

  <!-- 970 x 90 -->
  <div class="size-label" style="left:60px;top:1041px">970 X 90</div>
  <section class="banner" style="left:60px;top:1074px;width:776px;height:72px">
    <div class="art art--wide" style="width:310px" role="img" aria-label="Row of sketched houses with green gas"></div>
    <div class="headline" style="left:528px;top:37px;font-size:56px;-webkit-text-stroke-width:6px">GOT RADON?</div>
  </section>

  <!-- 160 x 600 -->
  <div class="size-label" style="left:882px;top:632px">160 X 600</div>
  <section class="banner" style="left:882px;top:666px;width:128px;height:480px">
    <div class="art art--tall" style="height:235px" role="img" aria-label="Stacked sketched houses with green radon gas"></div>
    <span class="letter" style="left:33px;top:262px">G</span>
    <span class="letter" style="left:33px;top:319px">O</span>
    <span class="letter" style="left:33px;top:378px">T</span>
    <span class="letter" style="left:83px;top:212px">R</span>
    <span class="letter" style="left:83px;top:259px">A</span>
    <span class="letter" style="left:83px;top:306px">D</span>
    <span class="letter" style="left:83px;top:352px">O</span>
    <span class="letter" style="left:83px;top:400px">N</span>
    <span class="letter" style="left:83px;top:446px">?</span>
  </section>

  <!-- 120 x 600 -->
  <div class="size-label" style="left:1054px;top:632px">120 X 600</div>
  <section class="banner" style="left:1054px;top:666px;width:96px;height:480px">
    <div class="art art--tall" style="height:235px" role="img" aria-label="Stacked sketched houses with green radon gas"></div>
    <span class="letter" style="left:27px;top:326px;transform:translate(-50%,-50%) rotate(-90deg);font-size:38px">GOT</span>
    <span class="letter" style="left:66px;top:210px">R</span>
    <span class="letter" style="left:66px;top:258px">A</span>
    <span class="letter" style="left:66px;top:303px">D</span>
    <span class="letter" style="left:66px;top:350px">O</span>
    <span class="letter" style="left:66px;top:398px">N</span>
    <span class="letter" style="left:66px;top:444px">?</span>
  </section>

</main>
</body>
</html>
```